Accounting business needs business card

I have a business card but need something better. I want the colour changed and the design to be better. I have uploaded a picture of my new sign that is grey in colour, i would like to incorporate these colours.

```html
<!DOCTYPE html>
<html lang="en">
<head>
<meta charset="utf-8">
<title>Ledgerly – Business Card</title>
<link href="https://fonts.googleapis.com/css2?family=Montserrat:wght@400;500;700&display=swap" rel="stylesheet">
<style>
  :root {
    --bg: #262626;
    --teal: #27b894;
    --teal-dark: #1fa583;
    --ink: #2b2b2b;
    --paper: #ffffff;
    --badge-grey: #d9d9d9;
    --badge-sky: #2fb4e6;
    --badge-navy: #1c5aa6;
    --badge-gold: #f4c300;
  }
  * { margin: 0; padding: 0; box-sizing: border-box; }
  html, body { width: 1200px; height: 930px; overflow: hidden; }
  body {
    background: var(--bg);
    font-family: 'Montserrat', sans-serif;
    position: relative;
  }
  .card {
    position: absolute;
    width: 600px;
    height: 340px;
    border-radius: 24px;
  }
  .card--front {
    left: 90px; top: 90px;
    background: var(--teal);
    display: flex; flex-direction: column; align-items: center; justify-content: center;
    gap: 22px;
  }
  .brand-mark {
    width: 96px; height: 96px;
    border: 3px solid currentColor;
    border-radius: 50%;
  }
  .brand-name {
    font-weight: 500;
    letter-spacing: 0.42em;
    text-transform: uppercase;
  }
  .card--front .brand { color: var(--paper); display: flex; flex-direction: column; align-items: center; gap: 24px; }
  .card--front .brand-name { font-size: 34px; padding-left: 0.42em; }

  .card--back {
    left: 510px; top: 500px;
    background: var(--paper);
    color: var(--ink);
  }
  .badges {
    position: absolute; top: 26px; right: 28px;
    display: flex; align-items: center; gap: 10px;
  }
  .badge-seal { width: 40px; height: 40px; border-radius: 50%; background: var(--badge-grey); }
  .badge-round { width: 52px; height: 52px; border-radius: 50%; background: var(--badge-sky); }
  .badge-flag { display: flex; width: 112px; height: 50px; }
  .badge-flag span:first-child { flex: 2; background: var(--badge-navy); }
  .badge-flag span:last-child { flex: 1; background: var(--badge-gold); }

  .card--back .brand {
    position: absolute; left: 40px; top: 70px;
    display: flex; flex-direction: column; align-items: flex-start; gap: 16px;
    color: var(--ink);
  }
  .card--back .brand-mark { width: 70px; height: 70px; border-width: 2.5px; margin-left: 20px; }
  .card--back .brand-name { font-size: 26px; }

  .rule { position: absolute; height: 1.5px; background: var(--teal); }
  .rule--top { right: 28px; top: 176px; width: 250px; }
  .rule--bottom { left: 40px; top: 250px; width: 300px; }

  .person {
    position: absolute; right: 30px; top: 188px;
    text-align: right;
  }
  .person-name { color: var(--teal); font-weight: 700; font-size: 24px; letter-spacing: 0.03em; text-transform: uppercase; }
  .person-line { font-size: 13px; font-weight: 500; margin-top: 4px; }

  .contact {
    position: absolute; left: 40px; top: 262px;
    list-style: none; font-size: 15px;
  }
  .contact li { display: flex; align-items: center; gap: 8px; line-height: 21px; }
  .contact svg { width: 12px; height: 12px; fill: none; stroke: var(--teal); stroke-width: 2; }
</style>
</head>
<body>
  <section class="card card--front">
    <div class="brand">
      <span class="brand-mark"></span>
      <span class="brand-name">Ledgerly</span>
    </div>
  </section>

  <section class="card card--back">
    <div class="badges">
      <span class="badge-seal" role="img" aria-label="Registered practitioner badge"></span>
      <span class="badge-round" role="img" aria-label="Software partner badge"></span>
      <span class="badge-flag" role="img" aria-label="Professional membership badge"><span></span><span></span></span>
    </div>

    <div class="brand">
      <span class="brand-mark"></span>
      <span class="brand-name">Ledgerly</span>
    </div>

    <div class="rule rule--top"></div>
    <div class="person">
      <p class="person-name">Owen Marlow</p>
      <p class="person-line">CPA, MTAX, BCOM (Acc &amp; Fin)</p>
      <p class="person-line">Taxation &amp; Business Accountant</p>
    </div>

    <div class="rule rule--bottom"></div>
    <ul class="contact">
      <li><svg viewBox="0 0 12 12"><path d="M2 1.5 L4.5 1.5 L5 4 L3.6 5 Q5 7.6 7 8.4 L8 7 L10.5 7.5 L10.5 10 Q5 10.5 2 4 Z"/></svg>0400 555 182</li>
      <li><svg viewBox="0 0 12 12"><rect x="1" y="2.5" width="10" height="7"/><path d="M1 2.5 L6 6.5 L11 2.5"/></svg>owen@ledgerly.com.au</li>
      <li><svg viewBox="0 0 12 12"><circle cx="6" cy="6" r="5"/><path d="M1 6 H11 M6 1 Q3 6 6 11 Q9 6 6 1"/></svg>www.ledgerly.com.au</li>
    </ul>
  </section>
</body>
</html>
```